Business cards and stationary design

We just completed the design of our new logo and we need to print new business cards and letterhead for our nonprofit. We are looking for a fresh new design that shows off our new logo. On letterhead, we must have a column on the right or left to include our Board of Directors (up to 45 names) (see attachment)

Industry/Entity Type

Non-Profit

Contact Information for Business Card

Standard business card with name, title, Company name, mailing address phone numbers, email address and website. Tagline on back "Bringing the homeless home"

Font styles to use
Sans Serif

Requirements
Must have
• include pertinent information above
• new logo
• fonts compatible with logo
• should use logo colors only
Nice to have
• tag lines

```html
<!DOCTYPE html>
<html lang="en">
<head>
<meta charset="utf-8">
<title>Harbor Home Alliance – Business Card</title>
<link rel="stylesheet" href="https://fonts.googleapis.com/css2?family=Arimo:wght@400;700&display=swap">
<style>
  :root {
    --teal: #1b8fb0;
    --red: #d8262f;
    --yellow: #f6b82a;
    --ink: #4a4a4a;
    --card: #ffffff;
    --backdrop: #e9e7e3;
  }
  * { box-sizing: border-box; margin: 0; padding: 0; }
  html, body {
    width: 1200px; height: 911px; overflow: hidden;
    background: var(--backdrop);
    font-family: "Arimo", Arial, sans-serif;
  }
  .canvas { position: relative; width: 1200px; height: 911px; }
  .card {
    position: absolute;
    width: 525px; height: 300px;
    background: var(--card);
    box-shadow: 0 6px 18px rgba(0,0,0,0.18);
    overflow: hidden;
  }
  .card--front { left: 70px; top: 120px; }
  .card--back { left: 605px; top: 490px; }

  .name-tab {
    position: absolute; left: 0; top: 44px;
    width: 20px; height: 44px; background: var(--teal);
  }
  .person { position: absolute; left: 34px; top: 44px; }
  .person__name {
    color: var(--teal); font-size: 22px; font-weight: 400; letter-spacing: 0.5px;
  }
  .person__title {
    color: var(--red); font-size: 14px; margin-top: 4px; letter-spacing: 0.3px;
  }

  .contact {
    position: absolute; left: 130px; top: 168px;
    width: 180px;
    color: var(--ink); font-size: 12.5px; line-height: 18px;
    white-space: nowrap;
  }
  .contact__org { font-weight: 700; }
  .contact__row { display: flex; align-items: center; gap: 7px; }
  .contact__row svg { width: 12px; height: 12px; flex: none; }
  .contact__address { margin-bottom: 6px; }

  .brand-panel {
    position: absolute; right: 0; top: 0;
    width: 195px; height: 300px;
    display: flex; flex-direction: column; align-items: flex-start; justify-content: center;
    padding-left: 24px; gap: 14px;
    border-left: 6px solid var(--red);
  }
  .brand-square { width: 30px; height: 30px; background: var(--yellow); flex: none; }
  .brand-name {
    color: var(--teal); font-size: 24px; font-weight: 700; line-height: 1.15; letter-spacing: 1px;
  }

  .back-brand {
    position: absolute; inset: 0;
    display: flex; align-items: center; justify-content: center; gap: 14px;
  }
  .back-brand .brand-name { font-size: 28px; }
</style>
</head>
<body>
<main class="canvas">
  <section class="card card--front" aria-label="Business card front">
    <div class="name-tab"></div>
    <div class="person">
      <p class="person__name">MARA QUILL</p>
      <p class="person__title">CEO/FOUNDER</p>
    </div>
    <div class="contact">
      <div class="contact__address">
        <p class="contact__org">Harbor Home Alliance</p>
        <p>412 Alder Creek Road</p>
        <p>Fairview, Alaska 99510</p>
      </div>
      <p class="contact__row">
        <svg viewBox="0 0 12 12" aria-hidden="true"><path d="M3 1l2 2.5-1.2 1.3c.7 1.5 1.9 2.7 3.4 3.4L8.5 7 11 9l-1 2C5 11 1 7 1 2z" fill="var(--teal)"/></svg>
        555 210 4476
      </p>
      <p class="contact__row">
        <svg viewBox="0 0 12 12" aria-hidden="true"><rect x="1" y="2.5" width="10" height="7" fill="var(--teal)"/><path d="M1 2.5l5 4 5-4" stroke="#fff" fill="none"/></svg>
        mara@harborhome.org
      </p>
      <p class="contact__row">
        <svg viewBox="0 0 12 12" aria-hidden="true"><circle cx="6" cy="6" r="5" fill="var(--teal)"/><path d="M1 6h10M6 1c2 2 2 8 0 10M6 1c-2 2-2 8 0 10" stroke="#fff" stroke-width=".8" fill="none"/></svg>
        www.harborhome.org
      </p>
    </div>
    <div class="brand-panel">
      <span class="brand-square"></span>
      <p class="brand-name">HARBOR<br>HOME<br>ALLIANCE</p>
    </div>
  </section>

  <section class="card card--back" aria-label="Business card back">
    <div class="back-brand">
      <span class="brand-square"></span>
      <p class="brand-name">HARBOR HOME ALLIANCE</p>
    </div>
  </section>
</main>
</body>
</html>
```